Brightwave Reach - Business Card

We need a business card for a Social Media Marketing company that specializes in online marketing for small businesses in Canada using common Social Media platforms such as Pixlora, Chatterly, Blinkpost & Quibber.

I have uploaded a copy of our logo which I would like utilized in the business card. We would like the business card to be modern yet classy design.

Our website is www.brightwavereach.ca

Industry/Entity Type

Marketing

Contact Information for Business Card

Email: info@brightwavereach.ca
Website: www.brightwavereach.ca
Telephone: 604-555-0193

Colors

Designer to choose colors to be used in the design.

Requirements
Must have
• Social Media icons on reverse
• Please add some designs with color.

```html
<!DOCTYPE html>
<html lang="en">
<head>
<meta charset="utf-8">
<title>Brightwave Reach – Business Card</title>
<link rel="stylesheet" href="https://fonts.googleapis.com/css2?family=Open+Sans:wght@400;600;800&display=swap">
<style>
  :root {
    --backdrop: #2b2c2d;
    --card-dark: #3b3f40;
    --card-light: #f4f4f4;
    --ink-dark: #3a3d3e;
    --ink-light: #ffffff;
    --rule: #8a8f90;
  }
  * { margin: 0; padding: 0; box-sizing: border-box; }
  html, body {
    width: 1200px; height: 960px; overflow: hidden;
    background: var(--backdrop);
    font-family: "Open Sans", Arial, sans-serif;
  }
  .canvas {
    position: relative; width: 1200px; height: 960px;
    display: flex; flex-direction: column; align-items: center; justify-content: center; gap: 60px;
  }
  .card {
    position: relative; width: 700px; height: 400px; overflow: hidden;
    box-shadow: 0 12px 30px rgba(0,0,0,.45);
  }

  /* Reverse side */
  .card-back { background: var(--card-dark); }
  .back-brand {
    position: absolute; top: 120px; left: 0; right: 0; text-align: center;
    color: var(--ink-light); font-weight: 800; font-size: 38px; letter-spacing: 1px; text-transform: uppercase;
  }
  .social-row {
    position: absolute; top: 272px; left: 60px; right: 60px;
    display: flex; align-items: center; gap: 18px;
  }
  .social-row .rule { flex: 1; height: 1px; background: var(--rule); }
  .social-item {
    display: flex; align-items: center; gap: 7px;
    color: var(--ink-light); font-size: 14px; font-weight: 600;
  }
  .social-item .dot {
    width: 22px; height: 22px; border: 1.5px solid var(--ink-light); border-radius: 50%;
  }

  /* Front side */
  .card-front { background: var(--card-light); }
  .front-brand {
    position: absolute; top: 70px; left: 0; right: 0;
    display: flex; justify-content: center; align-items: center; gap: 14px;
    color: var(--ink-dark); font-weight: 800; font-size: 42px; text-transform: uppercase; letter-spacing: 1px;
  }
  .front-brand .mark { width: 18px; height: 18px; background: var(--ink-dark); }
  .contact-band {
    position: absolute; left: 0; right: 0; top: 205px; bottom: 0;
    background: var(--card-dark);
  }
  .contact-band .edge-line {
    position: absolute; left: 0; right: 0; top: 12px; height: 3px; background: var(--ink-light);
  }
  .contact {
    position: absolute; top: 50px; left: 150px; color: var(--ink-light);
  }
  .contact .person { font-size: 20px; font-weight: 600; text-transform: uppercase; }
  .contact .person .role { font-weight: 400; }
  .contact .lines { margin-top: 8px; font-size: 16px; }
  .contact .lines b { font-weight: 800; }
  .contact .web { margin-top: 6px; font-size: 17px; letter-spacing: 6px; }
</style>
</head>
<body>
<main class="canvas">
  <section class="card card-back" aria-label="Card reverse">
    <div class="back-brand">Brightwave Reach</div>
    <div class="social-row">
      <span class="rule"></span>
      <span class="social-item"><span class="dot"></span>Chatterly</span>
      <span class="social-item"><span class="dot"></span>Pixlora</span>
      <span class="social-item"><span class="dot"></span>Quibber</span>
      <span class="rule"></span>
    </div>
  </section>

  <section class="card card-front" aria-label="Card front">
    <div class="front-brand"><span class="mark"></span>Brightwave Reach</div>
    <div class="contact-band">
      <span class="edge-line"></span>
      <div class="contact">
        <p class="person">Daniel Reyes <span class="role">- CEO/Founder</span></p>
        <p class="lines"><b>Phone :</b> 604-555-0193 &nbsp;<b>Email :</b> info@brightwavereach.ca</p>
        <p class="web">www.brightwavereach.ca</p>
      </div>
    </div>
  </section>
</main>
</body>
</html>
```